Overnight youth camp for refugee kids needs a brochure in Arabic

We need a 3-fold "Z" brochure for an overnight youth camp for Arabic speaking teens in Canada from the Middle East and Africa. The camp's name is Camp Wrenfell. Design should have an outdoors, sports theme and be attractive to teens and their parents. We will supply pictures and text in English. All but the Camp Wrenfell name should be in Arabic.

```html
<!DOCTYPE html>
<html lang="ar">
<head>
<meta charset="utf-8">
<title>Camp Wrenfell – Trifold Brochure</title>
<link rel="stylesheet" href="https://fonts.googleapis.com/css2?family=Lalezar&family=Changa:wght@400;700&display=swap">
<style>
:root{
  --green:#5cc433;
  --green-dark:#3f9a22;
  --ink:#232323;
  --charcoal:#2e2e2e;
  --paper:#ffffff;
  --stage:#d9d9d9;
  --teal:#4fb3b0;
  --water:#4f86b8;
  --grass:#6f9a45;
  --text:#1e1e1e;
}
*{box-sizing:border-box;margin:0;padding:0}
html,body{width:757px;height:1200px;overflow:hidden}
body{background:var(--stage);position:relative;font-family:"Changa",sans-serif;color:var(--text)}
.sheet{position:absolute;left:43px;width:672px;background:var(--paper);overflow:hidden;box-shadow:0 3px 8px rgba(0,0,0,.35)}
.sheet--outer{top:26px;height:547px}
.sheet--inner{top:612px;height:536px}
.panel{position:absolute;top:0;width:224px;height:100%;overflow:hidden}
.panel--1{left:0}.panel--2{left:224px}.panel--3{left:448px}
.panel--dark{background:var(--charcoal);color:#fff}
.abs{position:absolute}
.photo{position:absolute}
.ar{direction:rtl;text-align:right;font-size:7.4px;line-height:1.5}
.ar--light{color:#fff;font-size:9px;line-height:1.6;text-align:justify}
.headline{font-family:"Lalezar",sans-serif;direction:rtl;text-align:center;color:var(--ink);line-height:1.1}
.brand-circle{position:absolute;border-radius:50%;background:var(--paper);border:3px solid var(--ink);display:flex;align-items:center;justify-content:center;text-align:center}
.brand-name{font-family:"Changa",sans-serif;font-weight:700;color:var(--green);line-height:1}
.site{position:absolute;bottom:2px;left:0;width:224px;text-align:center;font-size:9px;font-weight:700;color:var(--ink);font-family:"Changa",sans-serif;direction:ltr}
.pill{position:absolute;left:30px;width:164px;height:17px;border-radius:9px;background:var(--green);color:#fff;font-weight:700;font-size:10px;display:flex;align-items:center;justify-content:center;gap:5px;direction:ltr}
.ticks{list-style:none;direction:rtl}
.ticks li{display:flex;align-items:center;gap:4px;font-size:7.2px;line-height:1.75}
.tick{width:8px;height:8px;flex:none}
.hl{color:var(--green)}
.contact{direction:ltr;font-size:6.2px;color:#fff;display:flex;gap:5px;align-items:flex-start;margin-bottom:5px}
</style>
</head>
<body>

<!-- ================= OUTER SIDE ================= -->
<section class="sheet sheet--outer">

  <!-- Panel 1 : activities -->
  <div class="panel panel--1">
    <div class="photo" role="img" aria-label="Teens in life jackets riding a motorboat on a lake" style="left:0;top:0;width:224px;height:230px;background:linear-gradient(160deg,#8fb8d8,#3f74a8 60%,#2c5a86)"></div>
    <svg class="abs" style="left:0;top:0" width="224" height="547" viewBox="0 0 224 547">
      <path d="M0 215 C60 250 150 255 224 200 L224 250 L0 250Z" fill="#fff"/>
      <path d="M0 200 C50 232 150 240 224 188 L224 198 C150 250 60 240 0 212Z" fill="var(--green)"/>
      <path d="M0 232 C70 262 160 250 224 210 L224 218 C160 258 70 268 0 240Z" fill="var(--charcoal)"/>
      <path d="M0 500 C70 470 150 440 224 462 L224 547 L0 547Z" fill="var(--charcoal)"/>
      <path d="M0 494 C70 462 150 434 224 454 L224 462 C150 442 70 472 0 502Z" fill="#fff"/>
      <path d="M0 505 C70 476 150 450 224 470 L224 476 C150 456 70 482 0 511Z" fill="var(--green)"/>
    </svg>
    <div class="photo" role="img" aria-label="Round photo of a smiling boy splashing in the water" style="left:18px;top:186px;width:96px;height:96px;border-radius:50%;border:3px solid #fff;background:radial-gradient(circle at 40% 40%,#bcd8ea,#4a86bd)"></div>
    <div class="abs ar" style="left:22px;top:283px;width:190px">القيم المسيحية هي أساس فعالياتنا ومغامراتنا كل يوم في هذا المخيم. نحن حريصون على تزويد كل المشتركين والمشتركات بهذا المخيم بالذكريات والتجارب التي لم ينسوها طوال حياتهم بالإضافة إلى الصداقات التي سوف تبدأ هنا وتستمر معهم حتى بعد مغادرتهم المخيم.</div>
    <div class="abs headline" style="left:20px;top:344px;width:194px;font-size:10px;text-align:right">برنامجنا يتضمن كل من <span class="hl">الفعاليات</span> الآتية :</div>
    <ul class="abs ticks" style="left:30px;top:362px;width:186px">
      <li><svg class="tick" viewBox="0 0 10 10"><circle cx="5" cy="5" r="4.3" fill="none" stroke="var(--green)"/><path d="M3 5.2l1.4 1.4L7 3.8" fill="none" stroke="var(--green)" stroke-width="1.2"/></svg>السباحة</li>
      <li><svg class="tick" viewBox="0 0 10 10"><circle cx="5" cy="5" r="4.3" fill="none" stroke="var(--green)"/><path d="M3 5.2l1.4 1.4L7 3.8" fill="none" stroke="var(--green)" stroke-width="1.2"/></svg>ألعاب الميدان</li>
      <li><svg class="tick" viewBox="0 0 10 10"><circle cx="5" cy="5" r="4.3" fill="none" stroke="var(--green)"/><path d="M3 5.2l1.4 1.4L7 3.8" fill="none" stroke="var(--green)" stroke-width="1.2"/></svg>الحرف الفنية</li>
      <li><svg class="tick" viewBox="0 0 10 10"><circle cx="5" cy="5" r="4.3" fill="none" stroke="var(--green)"/><path d="M3 5.2l1.4 1.4L7 3.8" fill="none" stroke="var(--green)" stroke-width="1.2"/></svg>القوارب والتجديف</li>
      <li><svg class="tick" viewBox="0 0 10 10"><circle cx="5" cy="5" r="4.3" fill="none" stroke="var(--green)"/><path d="M3 5.2l1.4 1.4L7 3.8" fill="none" stroke="var(--green)" stroke-width="1.2"/></svg>التسلق</li>
      <li><svg class="tick" viewBox="0 0 10 10"><circle cx="5" cy="5" r="4.3" fill="none" stroke="var(--green)"/><path d="M3 5.2l1.4 1.4L7 3.8" fill="none" stroke="var(--green)" stroke-width="1.2"/></svg>التجمع حول شعلة النار ليلا</li>
      <li><svg class="tick" viewBox="0 0 10 10"><circle cx="5" cy="5" r="4.3" fill="none" stroke="var(--green)"/><path d="M3 5.2l1.4 1.4L7 3.8" fill="none" stroke="var(--green)" stroke-width="1.2"/></svg>مهارات العيش في الطبيعة والهواء الطلق</li>
    </ul>
    <div class="abs" style="left:30px;top:500px;display:flex;align-items:center;gap:5px">
      <span style="width:12px;height:12px;border-radius:50%;background:var(--green)"></span>
      <span class="brand-name" style="font-size:20px">Camp Wrenfell</span>
    </div>
    <div class="site" style="color:var(--paper)">www.campwrenfell.ca</div>
  </div>

  <!-- Panel 2 : location & contact -->
  <div class="panel panel--2 panel--dark">
    <div class="photo" role="img" aria-label="Faded photo of camp cabins among trees" style="left:0;top:0;width:224px;height:547px;background:linear-gradient(180deg,#3a3a3a,#2a2f2a 50%,#263026);opacity:.9"></div>
    <svg class="abs" style="left:0;top:0" width="224" height="140" viewBox="0 0 224 140">
      <path d="M0 0 L224 0 L224 40 C160 70 80 60 0 40Z" fill="#fff"/>
      <path d="M0 40 C80 60 160 70 224 40 L224 50 C160 82 80 72 0 50Z" fill="var(--green)"/>
    </svg>
    <div class="brand-circle" style="left:68px;top:10px;width:88px;height:88px"><span class="brand-name" style="font-size:15px">Camp<br>Wrenfell</span></div>
    <div class="abs ar ar--light" style="left:24px;top:160px;width:178px">المخيم يقع بالقرب من مدينة ترينتون، أونتاريو على بعد ساعتين من مدينة تورنتو و ساعات من مدينة أوتاوا و ساعات من مدينة لندن.<br><br>نحن حريصون على توفير كابينات نوم نظيفة ومريحة، قاعة طعام جديدة، صالة ألعاب رياضية، ملاعب رياضية، وساحل مشرف على البحيرة الخاصة بالمخيم.</div>
    <div class="photo" role="img" aria-label="Street map showing the camp location" style="left:60px;top:280px;width:110px;height:110px;border-radius:50%;border:4px solid var(--green);background:radial-gradient(circle,#f3f1ec,#dcd9d0)"></div>
    <div class="abs ar" style="left:24px;top:424px;width:184px;color:#fff;font-size:7px;line-height:1.45"><span class="hl" style="float:left;font-weight:700">13 - 8</span>للراغبين في التسجيل في المخيم من الفترة يوليو<br>، يرجى زيارتنا على الموقع الإلكتروني الآتي:</div>
    <div class="pill" style="top:452px"><svg width="9" height="9" viewBox="0 0 10 10"><circle cx="5" cy="5" r="4.2" fill="none" stroke="#fff"/><path d="M1 5h8M5 1c-2 2-2 6 0 8M5 1c2 2 2 6 0 8" fill="none" stroke="#fff" stroke-width=".8"/></svg>www.campwrenfell.ca</div>
    <div class="abs" style="left:70px;top:482px">
      <div class="contact"><svg width="7" height="8" viewBox="0 0 8 10"><path d="M4 0a3.5 3.5 0 0 1 3.5 3.5C7.5 6 4 10 4 10S.5 6 .5 3.5A3.5 3.5 0 0 1 4 0z" fill="#fff"/></svg><span>418 Birchline Road, Unit 7,<br>Fernbrook, Ontario K0A 2Z0</span></div>
      <div class="contact"><svg width="8" height="6" viewBox="0 0 10 7"><rect width="10" height="7" fill="#fff"/><path d="M0 0l5 4 5-4" fill="none" stroke="#555"/></svg><span>info@campwrenfell.ca</span></div>
      <div class="contact"><svg width="7" height="7" viewBox="0 0 10 10"><path d="M2 0l2 2.5-1.2 1.5a6 6 0 0 0 3.2 3.2L7.5 6 10 8l-1.5 2C4 10 0 6 0 1.5z" fill="#fff"/></svg><span>(555) 010-0495</span></div>
    </div>
    <div class="site" style="color:var(--ink);background:#fff;bottom:0;padding:2px 0">www.campwrenfell.ca</div>
  </div>

  <!-- Panel 3 : cover -->
  <div class="panel panel--3">
    <div class="photo" role="img" aria-label="Group of campers standing on a dock by the lake" style="left:0;top:135px;width:224px;height:245px;background:linear-gradient(180deg,#b9d4ea 0%,#8fb7d6 35%,#5f8a4a 52%,#6c92b4 62%,#3f6f9a)"></div>
    <svg class="abs" style="left:0;top:0" width="224" height="547" viewBox="0 0 224 547">
      <path d="M0 0H224V140C160 170 80 160 0 150Z" fill="#fff"/>
      <path d="M0 150C80 160 160 170 224 140V148C160 180 80 170 0 158Z" fill="var(--green)"/>
      <path d="M0 158C80 170 160 180 224 148V154C160 188 80 178 0 164Z" fill="var(--charcoal)"/>
      <path d="M0 380C70 360 150 380 224 405V547H0Z" fill="#fff"/>
      <path d="M0 372C70 352 150 372 224 398V405C150 380 70 360 0 380Z" fill="var(--green)"/>
      <path d="M0 364C70 344 150 364 224 390V398C150 372 70 352 0 372Z" fill="var(--charcoal)"/>
    </svg>
    <div class="brand-circle" style="left:55px;top:22px;width:114px;height:114px;border-width:4px"><span class="brand-name" style="font-size:19px">Camp<br>Wrenfell</span></div>
    <div class="abs headline" style="left:0;top:196px;width:224px;font-size:24px;color:var(--ink);text-shadow:0 0 3px #fff,0 0 3px #fff">مرحبا بفصل</div>
    <div class="abs headline" style="left:0;top:310px;width:224px;font-size:38px;color:#fff;-webkit-text-stroke:1px var(--ink)">الصيف الرائع</div>
    <div class="abs ar" style="left:14px;top:416px;width:196px;font-size:8.6px;text-align:center;font-weight:700;line-height:1.55">مغامرات ترفيهية في الهواء الطلق والطبيعة الخلابة تتضمن السباحة وقوارب التجديف وما غيرها من فعاليات أخرى مخيم صيفي للأولاد والبنات للأعمار</div
    ><div class="abs headline" style="left:0;top:480px;width:224px;font-size:17px">سنوات <span class="hl">9</span> الى <span class="hl">16</span> سنة</div>
    <div class="site">www.campwrenfell.ca</div>
  </div>
</section>

<!-- ================= INNER SIDE ================= -->
<section class="sheet sheet--inner">

  <div class="photo" role="img" aria-label="Campers kneeling on the grass building a rope web with a leader" style="left:0;top:0;width:449px;height:260px;background:linear-gradient(170deg,#8fae5c,#6f9a45 45%,#557a36)"></div>

  <!-- Panel 1 : meals & cost -->
  <div class="panel panel--1">
    <svg class="abs" style="left:0;top:0" width="224" height="536" viewBox="0 0 224 536">
      <path d="M0 235C60 260 150 265 224 240V536H0Z" fill="#fff"/>
      <path d="M0 226C60 252 150 258 224 232V240C150 265 60 260 0 235Z" fill="var(--green)"/>
      <path d="M0 490C70 460 150 430 224 452V536H0Z" fill="var(--charcoal)"/>
      <path d="M0 484C70 452 150 424 224 444V452C150 432 70 462 0 492Z" fill="#fff"/>
      <path d="M0 495C70 466 150 440 224 460V466C150 446 70 472 0 501Z" fill="var(--green)"/>
    </svg>
    <div class="photo" role="img" aria-label="Round photo of campers at an outdoor barbecue table" style="left:8px;top:135px;width:96px;height:96px;border-radius:50%;border:3px solid var(--green);background:radial-gradient(circle,#c9c2a4,#6f8f4c)"></div>
    <div class="photo" role="img" aria-label="Round photo of a volunteer serving food at the grill" style="left:112px;top:135px;width:96px;height:96px;border-radius:50%;border:3px solid var(--green);background:radial-gradient(circle,#b9a58a,#5b7a3d)"></div>
    <div class="abs ar" style="left:20px;top:256px;width:192px">سوف نقوم بتوفير وجبات طعام صحية خالية من لحم الخنزير ومشتقاته. عادة يتم تقديم الحبوب والفطائر والتوست الفرنسي على الفطور، وتقديم السندويشات والحساء مع الفواكه على الغداء، وتقديم السباغيتي والهمبرغر والنقانق على العشاء.</div>
    <div class="abs headline" style="left:20px;top:313px;width:192px;font-size:11px;text-align:right">التكلفة: <span class="hl" style="font-size:14px">$50</span> لكل استمارة لكل مشترك<br>و تشمل كل ما يلي :</div>
    <ul class="abs ticks" style="left:20px;top:352px;width:192px">
      <li><svg class="tick" viewBox="0 0 10 10"><circle cx="5" cy="5" r="4.3" fill="none" stroke="var(--green)"/><path d="M3 5.2l1.4 1.4L7 3.8" fill="none" stroke="var(--green)" stroke-width="1.2"/></svg>توفير وجبات الطعام والوجبات الخفيفة</li>
      <li><svg class="tick" viewBox="0 0 10 10"><circle cx="5" cy="5" r="4.3" fill="none" stroke="var(--green)"/><path d="M3 5.2l1.4 1.4L7 3.8" fill="none" stroke="var(--green)" stroke-width="1.2"/></svg>طهي الطعام والشاوي</li>
      <li><svg class="tick" viewBox="0 0 10 10"><circle cx="5" cy="5" r="4.3" fill="none" stroke="var(--green)"/><path d="M3 5.2l1.4 1.4L7 3.8" fill="none" stroke="var(--green)" stroke-width="1.2"/></svg>توفير العدات الرياضية واستعمال البحيرة</li>
      <li><svg class="tick" viewBox="0 0 10 10"><circle cx="5" cy="5" r="4.3" fill="none" stroke="var(--green)"/><path d="M3 5.2l1.4 1.4L7 3.8" fill="none" stroke="var(--green)" stroke-width="1.2"/></svg>توفير اللوازم الحرفية والفنية</li>
      <li><svg class="tick" viewBox="0 0 10 10"><circle cx="5" cy="5" r="4.3" fill="none" stroke="var(--green)"/><path d="M3 5.2l1.4 1.4L7 3.8" fill="none" stroke="var(--green)" stroke-width="1.2"/></svg>تزويد كل مشترك بصور المخيم على قرص ممغنط</li>
      <li><svg class="tick" viewBox="0 0 10 10"><circle cx="5" cy="5" r="4.3" fill="none" stroke="var(--green)"/><path d="M3 5.2l1.4 1.4L7 3.8" fill="none" stroke="var(--green)" stroke-width="1.2"/></svg>تزويد كل مشترك بصورة جماعية لكل المشتركين</li>
    </ul>
    <div class="abs" style="left:30px;top:488px;display:flex;align-items:center;gap:5px">
      <span style="width:12px;height:12px;border-radius:50%;background:var(--green)"></span>
      <span class="brand-name" style="font-size:20px">Camp Wrenfell</span>
    </div>
    <div class="site" style="color:var(--paper)">www.campwrenfell.ca</div>
  </div>

  <!-- Panel 2 : about -->
  <div class="panel panel--2">
    <svg class="abs" style="left:0;top:0" width="224" height="536" viewBox="0 0 224 536">
      <path d="M0 230C60 205 160 200 224 222V536H0Z" fill="var(--charcoal)"/>
      <path d="M0 222C60 197 160 192 224 214V222C160 200 60 205 0 230Z" fill="var(--green)"/>
    </svg>
    <div class="brand-circle" style="left:71px;top:160px;width:82px;height:82px"><span class="brand-name" style="font-size:14px">Camp<br>Wrenfell</span></div>
    <div class="abs ar ar--light" style="left:16px;top:250px;width:192px;font-size:8.8px;line-height:1.55">مخيم مع المبيت لمدة خمسة ليالي خصص للشباب من دول شمال أفريقيا والشرق الأوسط. الهدف الرئيسي من من المخيم هو التركيز على تطوير الشباب وتحفيزهم على أن يكونوا قادة المستقبل عن طريق إدخال تعاليم الله في حياة المشتركين. أملنا هو أن يغادر كل مشترك أو مشتركة هذا المخيم مع ذكريات رائعة سوف يتذكرونها طوال حياتهم والمزيد من الثقة بالنفس والتأكيد على قيمة الذات واحترام أكبر للآخرين وأنفسهم ومخلوقات الله وقدرة أكبر على إقامة صداقات جديدة والحفاظ عليها وفهم أعمق لوجود الله في حياتهم.</div>
    <div class="abs ar" style="left:24px;top:448px;width:184px;color:#fff;font-size:7px;line-height:1.45"><span class="hl" style="float:left;font-weight:700">13 - 8</span>للراغبين في التسجيل في المخيم من الفترة يوليو<br>، يرجى زيارتنا على الموقع الإلكتروني الآتي:</div>
    <div class="pill" style="top:478px"><svg width="9" height="9" viewBox="0 0 10 10"><circle cx="5" cy="5" r="4.2" fill="none" stroke="#fff"/><path d="M1 5h8M5 1c-2 2-2 6 0 8M5 1c2 2 2 6 0 8" fill="none" stroke="#fff" stroke-width=".8"/></svg>www.campwrenfell.ca</div>
    <div class="site" style="color:var(--ink);background:#fff;bottom:0;padding:2px 0">www.campwrenfell.ca</div>
  </div>

  <!-- Panel 3 : goals -->
  <div class="panel panel--3">
    <div class="abs headline" style="left:16px;top:28px;width:196px;font-size:13px;text-align:right">نحن ملتزمون لتحقيق الأهداف<br>التالية :</div>
    <ul class="abs ticks" style="left:14px;top:76px;width:198px">
      <li style="align-items:flex-start;margin-bottom:9px;line-height:1.5"><svg class="tick" viewBox="0 0 10 10" style="margin-top:2px"><circle cx="5" cy="5" r="4.3" fill="none" stroke="var(--green)"/><path d="M3 5.2l1.4 1.4L7 3.8" fill="none" stroke="var(--green)" stroke-width="1.2"/></svg>الحرص على حصول جميع المشتركين في المخيم على الراحة التامة من خلال توفير الأماكن المخصصة للإقامة، واختيار الأشخاص الذين سوف يقيمون معهم في غرفهم، وتوفير البرامج الترفيهية والأشخاص المشرفين عليهم.</li>
      <li style="align-items:flex-start;margin-bottom:9px;line-height:1.5"><svg class="tick" viewBox="0 0 10 10" style="margin-top:2px"><circle cx="5" cy="5" r="4.3" fill="none" stroke="var(--green)"/><path d="M3 5.2l1.4 1.4L7 3.8" fill="none" stroke="var(--green)" stroke-width="1.2"/></svg>الحرص على التواصل مع كل مشترك ومساعدة كل الأولاد والبنات على التواصل فيما بينهم والبيئة المحيطة بهم.</li>
      <li style="align-items:flex-start;margin-bottom:9px;line-height:1.5"><svg class="tick" viewBox="0 0 10 10" style="margin-top:2px"><circle cx="5" cy="5" r="4.3" fill="none" stroke="var(--green)"/><path d="M3 5.2l1.4 1.4L7 3.8" fill="none" stroke="var(--green)" stroke-width="1.2"/></svg>الحرص على أن المشرفين على المخيم أن يكونوا مدركين أن كل مشترك أو مشتركة هم الهدف الرئيسي من المخيم وهم يستحقون منا كل الرعاية والعناية والاهتمام أينما كانوا ليلا ونهارا.</li>
      <li style="align-items:flex-start;line-height:1.5"><svg class="tick" viewBox="0 0 10 10" style="margin-top:2px"><circle cx="5" cy="5" r="4.3" fill="none" stroke="var(--green)"/><path d="M3 5.2l1.4 1.4L7 3.8" fill="none" stroke="var(--green)" stroke-width="1.2"/></svg>الحرص على أن يكون المخيم تجربة ممتعة وخبرة ذات مغزى لكل المشتركين.</li>
    </ul>
    <div class="photo" role="img" aria-label="Lakeside photo of a campfire circle with log benches under trees" style="left:0;top:335px;width:224px;height:185px;background:linear-gradient(180deg,#9ec3df 0%,#5f8f3f 35%,#7aa24e 70%,#6a9443)"></div>
    <div class="photo" role="img" aria-label="Round photo of campers sitting on the grass with a leader" style="left:10px;top:256px;width:100px;height:100px;border-radius:50%;border:3px solid var(--green);background:radial-gradient(circle,#a9c07c,#58803a)"></div>
    <div class="site">www.campwrenfell.ca</div>
  </div>
</section>

</body>
</html>
```